TA BRAMLEY BUSINESS CARD DESIGN PROJECT

We need to utilize our logo that was expertly created on PixelHarbor and now need to match this with a business card design.

```html
<!DOCTYPE html>
<html lang="en">
<head>
<meta charset="utf-8">
<title>TA BRAMLEY Business Card</title>
<link href="https://fonts.googleapis.com/css2?family=Montserrat:wght@400;500;700;800&display=swap" rel="stylesheet">
<style>
  :root {
    --brand-blue: #0f55a8;
    --ink: #2b2b2b;
    --card-white: #ffffff;
    --backdrop: #ebe6de;
  }
  * { margin: 0; padding: 0; box-sizing: border-box; }
  html, body { width: 1200px; height: 900px; overflow: hidden; }
  body {
    background: var(--backdrop);
    font-family: "Montserrat", sans-serif;
    position: relative;
  }
  .card {
    position: absolute;
    left: 310px;
    width: 582px;
    height: 332px;
    border-radius: 30px;
    overflow: hidden;
    box-shadow: 0 6px 14px rgba(0,0,0,0.18);
  }
  .card--front { top: 86px; background: var(--card-white); }
  .card--back { top: 470px; background: var(--brand-blue); }

  .brand-name {
    position: absolute;
    left: 0; right: 0;
    text-align: center;
    font-family: "Montserrat", sans-serif;
    font-weight: 800;
    letter-spacing: 0.12em;
    white-space: nowrap;
  }
  .card--front .brand-name { top: 110px; font-size: 56px; color: var(--brand-blue); }
  .card--back .brand-name { top: 128px; font-size: 62px; color: var(--card-white); }

  .holder {
    position: absolute;
    right: 317px;
    top: 218px;
    text-align: right;
    color: var(--ink);
  }
  .holder__name {
    font-weight: 700;
    font-size: 21px;
    color: var(--brand-blue);
    line-height: 1.2;
  }
  .holder__role { font-size: 15.5px; line-height: 1.4; }
  .holder__address { font-size: 15.5px; line-height: 1.35; margin-top: 4px; }

  .divider {
    position: absolute;
    left: 282px;
    top: 226px;
    width: 2px;
    height: 81px;
    background: var(--brand-blue);
  }

  .contact-list {
    position: absolute;
    left: 302px;
    top: 222px;
    list-style: none;
    color: var(--ink);
    font-size: 15.5px;
  }
  .contact-list li {
    display: flex;
    align-items: center;
    gap: 5px;
    height: 20.7px;
  }
  .contact-list svg { width: 13px; height: 13px; fill: var(--brand-blue); flex: none; }

  .base-band {
    position: absolute;
    left: 0; right: 0; bottom: 0;
    height: 11px;
    background: var(--brand-blue);
  }
</style>
</head>
<body>
  <section class="card card--front">
    <div class="brand-name">TA BRAMLEY</div>

    <div class="holder">
      <div class="holder__name">MARCUS HALE</div>
      <div class="holder__role">Managing Director</div>
      <div class="holder__address">Your address, City<br>State, Zip 1234</div>
    </div>

    <div class="divider"></div>

    <ul class="contact-list">
      <li>
        <svg viewBox="0 0 16 16" aria-hidden="true"><path d="M1 6c0-2 3-4 7-4s7 2 7 4v1h-4V5.5C10 5 6 5 5 5.5V7H1z"/><path d="M3 8h10l1 6H2z"/></svg>
        <span>123 456 789</span>
      </li>
      <li>
        <svg viewBox="0 0 16 16" aria-hidden="true"><path d="M4 1h7v4H4z"/><path d="M2 5h12v10H2zM5 8v1h2V8zm4 0v1h2V8zM5 11v1h2v-1zm4 0v1h2v-1z" fill-rule="evenodd"/></svg>
        <span>123 456 789</span>
      </li>
      <li>
        <svg viewBox="0 0 16 16" aria-hidden="true"><path d="M1 3h14v1L8 9 1 4z"/><path d="M1 6l7 5 7-5v7H1z"/></svg>
        <span>info@youremail.com</span>
      </li>
      <li>
        <svg viewBox="0 0 16 16" aria-hidden="true"><circle cx="8" cy="8" r="7"/><path d="M5 4c2 1 1 3 3 3s1 3-1 4c-1 1-2 0-2-2S3 6 5 4zm5-1c1 1 3 2 3 5-1-1-2 0-3-1s1-2 0-4z" fill="#fff"/></svg>
        <span>www.yourwebsite.com</span>
      </li>
    </ul>

    <div class="base-band"></div>
  </section>

  <section class="card card--back">
    <div class="brand-name">TA BRAMLEY</div>
  </section>
</body>
</html>
```